Brochure and Business Card design

I am looking for a high end, elegant A4, 4 page brochure booklet to convey our products to clientele that will be visiting a luxury display showroom.

Harrowgate Locks and Grilles is a Australian security provider, and we supply high end products from reputable brands.
The brochure will be directed to clients building a new home with a partnered building company and will be accompanied with display boards of our products.

I am providing files of a document we have put together with the relevant information and some images to help along the way, we are not bound by the layout or style it has been drawn up and we wish to give you complete creative freedom putting the peaces together. I have also provided the files for our logo in two different colours, and a picture of a brochure we love the look of.

If you have any suggestions, we can likely come up with further images etc if it will help or even if you feel some should be removed, we are open to that also

Target Market(s)

Young familys, people building new luxury homes, proffesionals, home owners

Industry/Entity Type

Business

Font styles to use
Serif
Sans Serif

Requirements
Must have
• All 8 pages
Should not have
• Not really a fan of reds and similar.

```html
<!DOCTYPE html>
<html lang="en">
<head>
<meta charset="utf-8">
<title>Ducted Vacuum – Brochure Spread</title>
<link rel="stylesheet" href="https://fonts.googleapis.com/css2?family=Mulish:wght@300;400;700&display=swap">
<style>
:root{
  --backdrop:#a9a9a9;
  --page:#f8f8f8;
  --green:#8fbf45;
  --green-head:#8cc63f;
  --ink:#5a5a5a;
  --ink-dark:#333;
  --white:#ffffff;
  --photo-warm:#e7d8c6;
  --photo-warm2:#c9a98d;
  --canister:#4b5563;
  --canister-dark:#374151;
  --accessory:#5b5f63;
}
*{margin:0;padding:0;box-sizing:border-box}
html,body{width:1200px;height:576px;overflow:hidden;background:var(--backdrop)}
body{position:relative;font-family:"Mulish",sans-serif;color:var(--ink)}
.spread{position:absolute;left:76px;top:86px;width:1046px;height:404px}
.page-left{position:absolute;left:0;top:0;width:523px;height:404px;background:var(--white)}
.page-right{position:absolute;left:523px;top:0;width:523px;height:404px;background:var(--page);overflow:hidden}
.family-photo{position:absolute;left:0;top:0;width:520px;height:176px;
  background:linear-gradient(90deg,#f5f3ef 0%,var(--photo-warm) 45%,var(--photo-warm2) 70%,#ece6de 100%)}
.feature-band{position:absolute;left:0;top:180px;width:523px;height:224px;background:var(--green)}
.accessories-photo{position:absolute;left:18px;top:22px;width:170px;height:184px;
  background:linear-gradient(135deg,#6d7176,var(--accessory) 60%,#44484c);opacity:.55;border-radius:4px}
.feature-title{position:absolute;left:213px;top:44px;font-weight:300;font-size:30px;line-height:36px;color:var(--white);letter-spacing:.3px}
.feature-copy{position:absolute;left:213px;top:92px;width:262px;font-size:7.6px;line-height:11.6px;color:#eef6e2}
.feature-copy p+p{margin-top:11.6px}
.canister-photo{position:absolute;left:35px;top:38px;width:118px;height:242px;
  background:linear-gradient(90deg,var(--canister-dark),var(--canister) 40%,var(--canister-dark));border-radius:10px 10px 18px 18px}
.text-block{position:absolute;width:138px;font-size:6.8px;line-height:8px}
.health{left:187px;top:47px}
.cleaning{left:187px;top:226px}
.suction{left:345px;top:51px}
.cost{left:345px;top:182px}
.text-block h2{font-weight:700;font-size:9.6px;line-height:11px;color:var(--green-head);margin-bottom:5px}
.health h2{width:124px}
.text-block p{margin-bottom:8px}
.text-block strong{color:var(--ink-dark)}
</style>
</head>
<body>
<div class="spread">
  <section class="page-left">
    <div class="family-photo" role="img" aria-label="Photo of a smiling father with two children on a couch"></div>
    <div class="feature-band">
      <div class="accessories-photo" role="img" aria-label="Product photo of ducted vacuum hose, wand and floor tools"></div>
      <h1 class="feature-title">Ducted Vacuum</h1>
      <div class="feature-copy">
        <p>Ducted vacuums with Harrowgate Locks and Grilles are the perfect accessory for keeping you home as good as new. With various units ranging from the smaller 2Hp - 2 to 4 outlet unit for the smaller home up to the 4Hp – 5 to 8 outlet unit for larger two story homes and everything in between.</p>
        <p>Don’t get caught up wrestling with and dragging around a corded vacuum. Use a ducted system and all you’ll need to carry is the wand.</p>
      </div>
    </div>
  </section>
  <section class="page-right">
    <div class="canister-photo" role="img" aria-label="Product photo of a ducted vacuum power unit canister"></div>
    <div class="text-block health">
      <h2>A Southwind Vac ducted vacuum improves your health</h2>
      <p>Every day we breathe in billions of polluting particles around the home. In fact, <strong>the average house collects 18kg of dust a year!</strong> Along with other allergens this can have a major impact on health, especially for asthma and allergy sufferers.</p>
      <p>While portable vacuum cleaners appear to clean a room, they in fact release dust, bacteria and allergens back into the air. Southwind Vac ducted vacuum systems remove all vacuumed dust particles, allergens and noxious odours, creating a healthier living environment</p>
    </div>
    <div class="text-block cleaning">
      <h2>Faster Easier Cleaning</h2>
      <p>Ducted vacuum systems are versatile enough to be used just about anywhere. Carpets, hard floors, curtains, skirtings, staircases, cars and verandas can all be cleaned with a ducted vacuum system – even the family pet (yes, we have actually tested this – results differ from pet to pet!).</p>
      <p>The longer hose and convenient inlet valves of a ducted vacuum help you to reach all parts of your house effortlessly. A Southwind Vac ducted vacuum will speed up and simplify how you clean your home, giving you more time for the important things in life – you and your family.</p>
    </div>
    <div class="text-block suction">
      <h2>More Powerful Suction</h2>
      <p>A Southwind Vac ducted vacuum system <strong>has</strong> up to five times more power than most conventional portable vacuum cleaners.</p>
      <p>The heavy duty long-life motors used in all Southwind Vac systems ensure hard to shift dust and dirt will be removed from your valuable carpets, soft furnishings and other floor coverings, both protecting them and prolonging their lives. The ducted vacuum system also works well on curtains.</p>
    </div>
    <div class="text-block cost">
      <h2>The Cost Effective Cleaning Solution</h2>
      <p>Did you know that most ducted vacuum systems cost roughly the same as a high quality portable vacuum cleaner? The differences are that ducted vacuum systems last considerably longer (up to four times in fact), are more robust and require less maintenance. It all adds up to a more cost effective investment. Southwind Vac ducted vacuum systems are a semi-permanent feature and an excellent selling point for your home. Why? They not only make cleaning a breeze, they are built to last. That combination will increase the value of your home – well in excess of the original purchase price! As a ducted vacuum system is a semi-permanent structure in your house, it is covered under building insurance.</p>
    </div>
  </section>
</div>
</body>
</html>
```